Lone Star Wetland Flora Stewardship Guild

We need to design the home page of this new website. We would like a fun website design for provides as a resource for members and information for potential members.
Please design so that we can see a portion of background on each side on the website.
I just need the final design files psd no coding needed.
Attached is their logo (colors are not 100% set in stone either so can mess with those as I did in the quick mockup attached)
Attached is a pdf newsletter they send out, you can get a feel for them and what they are about. The design is crappy and we are here to fix that going forward and we are starting with the website.
Here are some quick example websites (design style is open)
- I attached a quick mockup i did just for a content visual but by all means do what you want.
- http://www.brightpathleaders.example/
- http://www.civicunityhub.example/
- http://preview.webskinvault.example/show.php?cat=layouts&host=skinbazaar&temp=novaline
- http://www.meadowkeep.example/
- http://www.urbangleaners.example/
- http://www.projectcozyknit.example/
here are some of the other chapters website (pretty bad!)
and here are some of the others:
- http://www.dwrvcs.example/
- http://kwfg.example/
- http://www.blvcg.example/
Content Items that need to be included:
1. Logo
2. Menu - home, about, members, resources, events, membership, contact
3. Become a member - button or action
4. social links - chatterloop, workweave, clipstream
5. banner - that needs to explain their purpose "Promoting environmental stewardship through operations, research, education and outreach" (or this can be worked into the design)
6. Upcoming event (s)
7. Advertisement - members can place an ad on the website, this can be a placeholder for now
8. newsletter signup
9. advertise with us - this link can be in the footer
30-60 years of age, succesfull (household budgets of 120K+ men and women that live in texas.
Education

```html
<!DOCTYPE html>
<html lang="en">
<head>
<meta charset="utf-8">
<title>Lone Star Wetland Flora Stewardship Guild</title>
<link href="https://fonts.googleapis.com/css2?family=Open+Sans:wght@400;600;700&display=swap" rel="stylesheet">
<style>
:root{
  --navy:#0d3480;
  --navy-dark:#072a6b;
  --red:#c4293b;
  --red-dark:#a91f31;
  --text:#333333;
  --muted:#888888;
  --rule:#dddddd;
  --white:#ffffff;
  --footer-text:#e6e6e6;
}
*{box-sizing:border-box;margin:0;padding:0}
html,body{width:1177px;height:1200px;overflow:hidden}
body{position:relative;font-family:"Open Sans",Arial,sans-serif;color:var(--text);background:#0a0604}
.page-backdrop{position:absolute;inset:0;background:
  radial-gradient(ellipse at 15% 12%,rgba(160,175,150,.55),transparent 45%),
  radial-gradient(ellipse at 90% 30%,rgba(150,165,130,.5),transparent 40%),
  linear-gradient(180deg,#6f7a5e 0%,#4d5238 22%,#2f3020 40%,#17120b 58%,#0a0604 75%)}
.site-header{position:absolute;left:178px;top:51px;width:822px;height:119px;background:var(--white)}
.brand{position:absolute;left:16px;top:22px;width:180px;display:flex;align-items:flex-start;gap:8px}
.brand-mark{width:14px;height:14px;background:var(--red);flex:none;margin-top:3px}
.brand-name{font-size:14px;font-weight:700;line-height:18px;color:var(--navy)}
.social{position:absolute;top:24px;display:block;width:30px;height:30px}
.social.chatterloop{left:489px;background:#2f5597}
.social.chirpline{left:529px;background:#4a9fd8}
.social.workweave{left:568px;background:#1f7bbd}
.social.clipstream{left:608px;background:#c4161c}
.join-btn{position:absolute;left:648px;top:19px;width:174px;height:39px;background:linear-gradient(180deg,var(--red),var(--red-dark));color:var(--white);font-size:11.5px;font-weight:600;text-decoration:none;display:flex;align-items:center;justify-content:center;gap:9px}
.main-nav{position:absolute;left:205px;top:74px;width:617px;height:45px;background:var(--navy);display:flex}
.main-nav a{color:var(--white);text-decoration:none;font-size:11px;font-weight:600;height:45px;display:flex;align-items:center;padding:0 18px}
.main-nav a.active{background:var(--navy-dark);padding:0 25px}
.content{position:absolute;left:178px;top:186px;width:822px;height:760px;background:var(--white)}
.hero{position:absolute;left:29px;top:28px;width:764px;height:352px;border:1px solid var(--rule);padding:3px}
.hero-photo{width:100%;height:100%;background:linear-gradient(180deg,#eef0e6 0%,#8fb25a 25%,#5f8a3a 45%,#a9b98a 60%,#4f6b3a 80%,#3d5a2e 100%)}
.hero-caption{position:absolute;left:23px;top:211px;width:480px;height:71px;background:rgba(225,228,220,.88);padding:13px 18px;font-size:15.5px;font-weight:600;line-height:20px;color:#1e1e1e}
.hero-dots{position:absolute;left:355px;top:318px;display:flex;gap:11px}
.hero-dots span{width:14px;height:14px;border-radius:50%;background:var(--navy);border:2px solid var(--white)}
.hero-dots span.current{background:var(--red)}
.panel-head{position:absolute;top:407px;width:241px;height:46px;background:var(--navy);color:var(--white);font-size:16px;font-weight:600;padding:12px 16px}
.about-head{left:29px}
.events-head{left:289px}
.about-text{position:absolute;left:29px;top:462px;width:243px;font-size:10.5px;line-height:20.1px;color:#3a3a3a}
.btn-red{position:absolute;background:linear-gradient(180deg,var(--red),var(--red-dark));color:var(--white);text-decoration:none;font-size:11.5px;font-weight:600;display:flex;align-items:center;justify-content:center}
.read-more{left:28px;top:680px;width:124px;height:42px}
.event{position:absolute;left:289px;width:242px;height:84px;border-bottom:1px solid var(--rule)}
.event-thumb{position:absolute;left:0;width:84px;height:54px}
.event-title{position:absolute;left:92px;width:152px;font-size:10.5px;line-height:15.2px;color:#222}
.event-date{position:absolute;left:97px;font-size:12px;font-weight:600;color:var(--red)}
.ad-slot{position:absolute;left:552px;top:414px;width:241px;height:313px;background:linear-gradient(180deg,#3d8fc4 0%,#1f3f66 30%,#1a1a1d 60%,#1a1a1d 79%,#dcdcdc 79%,#dcdcdc 100%)}
.ad-sponsor{position:absolute;right:14px;bottom:14px;font-size:17px;font-weight:700;color:#222}
.newsletter{position:absolute;left:178px;top:946px;width:822px;height:128px;background:var(--navy);padding:0 30px}
.newsletter h2{position:absolute;left:30px;top:20px;font-size:15.5px;font-weight:600;color:var(--white)}
.field{position:absolute;top:60px;width:214px;height:38px;background:#f4f4f4;border:2px solid #d8d8d8;font-family:inherit;font-size:12.5px;color:#777;padding:0 16px}
.field.name{left:30px}
.field.email{left:266px}
.subscribe{left:500px;top:59px;width:173px;height:40px;border:0;font-family:inherit}
.mailing{position:absolute;left:0;width:1177px;top:1098px;text-align:center;font-size:12px;color:var(--footer-text)}
.mailing .label{color:#d23a4a}
.footer-rule{position:absolute;left:178px;top:1138px;width:822px;height:1px;background:#3a3230}
.footer-link{position:absolute;left:178px;top:1161px;font-size:12px;color:#a9a9a9;text-decoration:none}
.copyright{position:absolute;right:179px;top:1161px;font-size:12px;color:#a9a9a9}
</style>
</head>
<body>
<div class="page-backdrop" role="img" aria-label="Blurred photo of lily pads floating on dark pond water"></div>

<header class="site-header">
  <div class="brand">
    <span class="brand-mark"></span>
    <span class="brand-name">Lone Star Wetland Flora Stewardship Guild</span>
  </div>
  <a class="social chatterloop" href="#" aria-label="chatterloop"></a>
  <a class="social chirpline" href="#" aria-label="chirpline"></a>
  <a class="social workweave" href="#" aria-label="workweave"></a>
  <a class="social clipstream" href="#" aria-label="clipstream"></a>
  <a class="join-btn" href="#">BECOME A MEMBER
    <svg width="15" height="15" viewBox="0 0 16 16" aria-hidden="true"><circle cx="8" cy="8" r="8" fill="#fff"/><path d="M4 8h7M8 4.5 11.5 8 8 11.5" stroke="#b52434" stroke-width="2" fill="none" stroke-linecap="round" stroke-linejoin="round"/></svg>
  </a>
  <nav class="main-nav">
    <a class="active" href="#">HOME</a>
    <a href="#">ABOUT</a>
    <a href="#">MEMBERS</a>
    <a href="#">RESOURCES</a>
    <a href="#">EVENTS</a>
    <a href="#">MEMBERSHIP</a>
    <a href="#">CONTACT</a>
  </nav>
</header>

<main class="content">
  <section class="hero">
    <div class="hero-photo" role="img" aria-label="Photo of a calm wetland pond framed by tall reeds and green trees"></div>
    <p class="hero-caption">Promoting environmental stewardship through operations, research, education and outreach</p>
    <div class="hero-dots"><span></span><span class="current"></span><span></span></div>
  </section>

  <h2 class="panel-head about-head">ABOUT LSWFSG</h2>
  <p class="about-text">Lorem ipsum dolor sit amet, consectetuer adipiscing elit, sed diam nonummy nibh euismo d tincidunt ut laoreet dolore magna aliquam erat volutpat. Ut wisi enim ad minim veniam, quis nostrud exerci tation ullamcorper suscipit lobortis nisl ut aliquip ex ea commodo consequat. Duis autem vel eum iriure dolor in hendrerit in vulputate velit esse molestie conse quat, vel illum dolore eu feugiat nulla facilisis at vero eros et accumsan.</p>
  <a class="btn-red read-more" href="#">READ MORE</a>

  <h2 class="panel-head events-head">UPCOMING EVENTS</h2>
  <article class="event" style="top:459px">
    <div class="event-thumb" style="top:12px;background:linear-gradient(180deg,#7d9a6a,#4f7a5a)" role="img" aria-label="Photo of reeds and lily pads"></div>
    <p class="event-title" style="top:15px">Lorem ipsum dolor sit amet, consectet uer adipiscing elit.</p>
    <p class="event-date" style="top:49px">AUG 12 2014</p>
  </article>
  <article class="event" style="top:543px">
    <div class="event-thumb" style="top:12px;background:linear-gradient(180deg,#a9c7e0,#6e9a4e 45%,#8a7a4a)" role="img" aria-label="Photo of a pond with lily pads and trees"></div>
    <p class="event-title" style="top:15px">Nam liber tempor cum soluta nobis eleifend option congue</p>
    <p class="event-date" style="top:49px">AUG 14 2014</p>
  </article>
  <article class="event" style="top:627px">
    <div class="event-thumb" style="top:12px;background:linear-gradient(180deg,#5a8fd0,#c9dcef 40%,#5a8a3a 60%,#3e6a8a)" role="img" aria-label="Photo of open marshland under a blue sky"></div>
    <p class="event-title" style="top:15px">Typi non habent claritatem insitam est usus legentis</p>
    <p class="event-date" style="top:49px">AUG 17 2014</p>
  </article>

  <aside class="ad-slot" role="img" aria-label="Member advertisement showing pond treatment product containers">
    <span class="ad-sponsor">ClearPond Labs</span>
  </aside>
</main>

<section class="newsletter">
  <h2>NEWSLETTER SIGNUP</h2>
  <input class="field name" type="text" placeholder="Name">
  <input class="field email" type="email" placeholder="Email Address">
  <button class="btn-red subscribe">SUBSCRIBE</button>
</section>

<p class="mailing"><span class="label">MAILING ADDRESS:</span> LSWFSG C/O CAL RENNER - TREASURER P.O. BOX 4410 MARBLE FALLS, TX 78654</p>
<div class="footer-rule"></div>
<a class="footer-link" href="#">Advertise with us</a>
<p class="copyright">Copyrights@2014 lswfsg. All Right Reserved.</p>
</body>
</html>
```